Harbor Crest Holdings Corporate Showcase

Provide an attractive Corporate Website for a boutique Investment Company to showcase our activities and corporate interests.

Our Company works across a number of Sectors including

Real Estate
E-Commerce
Healthcare
Beauty & Personal Care
Technology
Resources

Lets keep the personality

Modern
Global
Sophisticated
Calm
Interesting

Lets keep the pages with MINIMAL Words
Lets use Photos/ Imagery to tell the story

We'll need a Banner Menu -
About Us
Expertise
Global Outlook
Sectors
Management
Media
Contact Us

Many thanks
Best wishes
Dennis.

Target Market(s)

Investors
Clients

Coding

Coded - Design and coding required

Number of Pages Required

5+ page

Font styles to use
Sans Serif

Colors
886aae
3176b5
00a990
f68e4d
f04a50
e667a6

Requirements
Must have
• WordPress Coding

Checkout this Website for look and feel - its cool:
www.qvr-example.com

Harbor Crest Partners
(Harbor Crest Holdings LLP)
London
E9 4ZX
United Kingdom

www.HarborCrestPartners-example.com
Nice to have
• Sophisticated colour palette - black/ brown/ blue/ purple/

```html
<!DOCTYPE html>
<html lang="en">
<head>
<meta charset="utf-8">
<title>Harbor Crest Holdings</title>
<link rel="stylesheet" href="https://fonts.googleapis.com/css2?family=Raleway:wght@400;500;600;700;800&family=Roboto:wght@400;500&display=swap">
<style>
:root{
  --purple:#886aae;
  --teal:#00a990;
  --teal-band:#14a88f;
  --pink:#e667a6;
  --line:#d79bb4;
  --ink:#2b2b2b;
  --grey:#777;
  --white:#fff;
}
*{box-sizing:border-box;margin:0;padding:0}
html,body{width:1200px;height:4218px;overflow:hidden}
body{position:relative;background:var(--white);font-family:'Roboto',sans-serif;color:var(--ink)}
.abs{position:absolute}
.heading{font-family:'Raleway',sans-serif;font-weight:600;color:var(--purple);text-align:center;letter-spacing:.5px}
.btn{position:absolute;width:157px;height:54px;border:2px solid var(--teal);border-radius:27px;color:var(--teal);font-family:'Raleway',sans-serif;font-size:15px;font-weight:500;display:flex;align-items:center;justify-content:center;text-transform:uppercase;background:var(--white)}
.vline{position:absolute;width:2px;background:var(--line)}
.hline{position:absolute;height:2px;background:var(--line)}

/* hero */
.hero{left:0;top:0;width:1200px;height:615px;background:linear-gradient(160deg,#9b7b5e 0%,#b9a98f 30%,#c9c4b5 50%,#8f9a78 75%,#67753f 100%)}
.nav-bar{left:0;top:0;width:1200px;height:72px;background:rgba(40,40,40,.45);display:flex;align-items:center}
.brand{position:absolute;left:110px;top:22px;display:flex;align-items:center;gap:10px;color:var(--white);font-family:'Raleway',sans-serif;font-size:22px;font-weight:500;letter-spacing:.5px}
.brand-mark{width:22px;height:22px;background:var(--white)}
.menu{position:absolute;right:110px;top:33px;display:flex;gap:21px;font-family:'Roboto',sans-serif;font-size:11.5px;color:var(--white)}
.menu .active{color:var(--teal)}
.hero-title{left:110px;top:306px;font-family:'Raleway',sans-serif;font-weight:800;font-size:28px;color:var(--white);letter-spacing:.5px}
.play{left:112px;top:359px;display:flex;align-items:center;gap:8px;color:var(--pink);font-family:'Raleway',sans-serif;font-size:19px}

/* works */
.works-title{left:0;top:710px;width:1200px;font-size:42px}
.work{position:absolute;width:290px;text-align:center}
.work-icon{display:block;margin:0 auto;width:70px;height:70px}
.work-label{font-family:'Raleway',sans-serif;font-size:15px;font-weight:500;margin-top:12px;letter-spacing:.3px}
.work-text{font-size:11px;line-height:25.5px;color:var(--grey);margin-top:4px}

/* about */
.about-kicker{left:110px;top:1556px;font-family:'Raleway',sans-serif;font-style:italic;font-size:24px;color:var(--teal)}
.about-title{left:110px;top:1600px;width:380px;font-family:'Raleway',sans-serif;font-size:24px;line-height:35px;color:var(--ink)}
.about-title span{color:var(--purple);font-weight:600}
.about-text{left:110px;top:1694px;width:392px;font-size:14.5px;line-height:31.8px;color:var(--grey);text-align:justify}
.photo{position:absolute;box-shadow:0 4px 14px rgba(0,0,0,.18)}

/* management */
.mgmt{left:0;top:2081px;width:1200px;height:514px;background:linear-gradient(135deg,#1bb29a,#0d9f86 60%,#13a88f)}
.mgmt-title{left:0;top:2182px;width:1200px;font-family:'Raleway',sans-serif;font-size:40px;font-weight:600;color:var(--white);text-align:center;letter-spacing:1px}
.mgmt-text{left:105px;top:2262px;width:990px;font-size:14.5px;line-height:34px;color:var(--white);text-align:center}
.btn-light{border-color:var(--white);color:var(--white);background:transparent}

/* global */
.global-title{left:598px;top:2768px;font-family:'Raleway',sans-serif;font-size:40px;color:var(--ink)}
.global-title span{color:var(--purple);font-weight:600}
.global-text{left:600px;top:2847px;width:480px;font-size:14.5px;line-height:31.8px;color:var(--grey);text-align:justify}

/* expertise */
.exp-title{left:0;top:3295px;width:1200px;font-size:40px}
.card{position:absolute;top:3369px;width:240px;height:274px}
.card-hover{background:linear-gradient(180deg,rgba(20,168,143,.92),rgba(0,169,144,.88));color:var(--white);text-align:center;padding-top:38px}
.card-name{font-family:'Raleway',sans-serif;font-size:21px;font-weight:600}
.card-role{font-size:12.5px;margin-top:4px}
.card-text{font-size:11px;line-height:23px;margin:16px 14px 0}
.socials{display:flex;justify-content:center;gap:10px;margin-top:12px}
.socials i{width:36px;height:36px;border-radius:50%}

/* footer */
.footer{left:0;top:3747px;width:1200px;height:471px;background:var(--purple);color:var(--white)}
.f-col{position:absolute;top:3820px}
.f-head{font-family:'Raleway',sans-serif;font-size:17px;font-weight:600;letter-spacing:.3px;margin-bottom:18px}
.f-links{list-style:none;font-size:13px;line-height:31.8px}
.newsletter{left:776px;top:3873px;width:312px;height:48px;background:var(--white);border-radius:24px;display:flex;align-items:center;justify-content:space-between;padding:0 18px 0 27px;font-size:12.5px;color:#777}
.contact{display:flex;align-items:center;gap:14px;font-size:15px}
.contact .dot{width:38px;height:38px;border-radius:50%;background:var(--teal);display:flex;align-items:center;justify-content:center}
.copy{left:0;top:4156px;width:1200px;text-align:center;font-size:14px}
.copy span{color:var(--teal)}
</style>
</head>
<body>

<!-- hero -->
<div class="abs hero" role="img" aria-label="Photo of two business people walking along a path between modern buildings"></div>
<div class="abs nav-bar"></div>
<div class="brand"><span class="brand-mark"></span>HARBOR CREST</div>
<nav class="menu">
  <span class="active">HOME</span><span>ABOUT US</span><span>EXPERTISE</span><span>GLOBAL OUTLOOK</span><span>SECTORS</span><span>MANAGEMENT</span><span>MEDIA</span><span>CONTACT US</span>
</nav>
<h1 class="abs hero-title">HARBOR CREST HOLDINGS</h1>
<div class="abs play">
  <svg width="24" height="24" viewBox="0 0 24 24"><circle cx="12" cy="12" r="12" fill="#e667a6"/><path d="M9 7l8 5-8 5z" fill="#fff"/></svg>
  Play Video
</div>

<!-- works -->
<h2 class="abs heading works-title">OUR COMPANY WORKS</h2>

<div class="work" style="left:105px;top:806px">
  <svg class="work-icon" viewBox="0 0 70 70" fill="none" stroke="#886aae" stroke-width="2"><circle cx="22" cy="12" r="7"/><path d="M10 60V32q0-8 12-8t12 8v28M16 60V44M28 60V44"/><path d="M40 30l10-10 10 10v16H40z"/><rect x="46" y="36" width="8" height="10"/></svg>
  <div class="work-label">REAL ESTATE</div>
  <p class="work-text">Nemo enim ipsam voluptatem quia voluptas sit aspernatur aut odit aut fugit, sed quia consequuntur magni dolores eos qui ratione voluptatem sequi nesciunt</p>
</div>
<div class="work" style="left:454px;top:806px">
  <svg class="work-icon" viewBox="0 0 70 70" fill="none" stroke="#886aae" stroke-width="2"><rect x="6" y="6" width="58" height="50" rx="3"/><path d="M6 16h58"/><circle cx="12" cy="11" r="1.5"/><circle cx="18" cy="11" r="1.5"/><path d="M18 26h4l5 16h20l4-12H25"/><circle cx="30" cy="48" r="2.5"/><circle cx="44" cy="48" r="2.5"/></svg>
  <div class="work-label">E-COMMERCE</div>
  <p class="work-text">Nemo enim ipsam voluptatem quia voluptas sit aspernatur aut odit aut fugit, sed quia consequuntur magni dolores eos qui ratione voluptatem sequi nesciunt</p>
</div>
<div class="work" style="left:802px;top:806px">
  <svg class="work-icon" viewBox="0 0 70 70" fill="none" stroke="#886aae" stroke-width="2"><path d="M35 62C10 44 4 32 6 22 8 10 24 6 35 18 46 6 62 10 64 22c2 10-4 22-29 40z"/><path d="M30 24h10v8h8v10h-8v8H30v-8h-8V32h8z"/></svg>
  <div class="work-label">HEALTHCARE</div>
  <p class="work-text">Nemo enim ipsam voluptatem quia voluptas sit aspernatur aut odit aut fugit, sed quia consequuntur magni dolores eos qui ratione voluptatem sequi nesciunt</p>
</div>

<div class="work" style="left:105px;top:1133px">
  <svg class="work-icon" viewBox="0 0 70 70" fill="none" stroke="#886aae" stroke-width="2"><circle cx="35" cy="16" r="6"/><path d="M27 44V28q0-6 8-6t8 6v16"/><path d="M8 44h54v10H8zM14 54v8M56 54v8M20 44v-6h10"/></svg>
  <div class="work-label">BEAUTY &amp; PERSONAL CARE</div>
  <p class="work-text">Nemo enim ipsam voluptatem quia voluptas sit aspernatur aut odit aut fugit, sed quia consequuntur magni dolores eos qui ratione voluptatem sequi nesciunt</p>
</div>
<div class="work" style="left:454px;top:1133px">
  <svg class="work-icon" viewBox="0 0 70 70" fill="none" stroke="#886aae" stroke-width="2"><circle cx="35" cy="30" r="24"/><ellipse cx="35" cy="30" rx="11" ry="24"/><path d="M11 30h48M15 18h40M15 42h40M35 54v10M27 54l-4 10M43 54l4 10"/></svg>
  <div class="work-label">TECHNOLOGY</div>
  <p class="work-text">Nemo enim ipsam voluptatem quia voluptas sit aspernatur aut odit aut fugit, sed quia consequuntur magni dolores eos qui ratione voluptatem sequi nesciunt</p>
</div>
<div class="work" style="left:802px;top:1133px">
  <svg class="work-icon" viewBox="0 0 70 70" fill="none" stroke="#886aae" stroke-width="2"><rect x="6" y="6" width="22" height="16"/><rect x="40" y="6" width="24" height="22"/><rect x="12" y="38" width="20" height="24"/><circle cx="52" cy="14" r="4"/><circle cx="22" cy="48" r="4"/><path d="M28 14h12M40 28l-12 14M44 62V44h16v18"/></svg>
  <div class="work-label">RESOURCES</div>
  <p class="work-text">Nemo enim ipsam voluptatem quia voluptas sit aspernatur aut odit aut fugit, sed quia consequuntur magni dolores eos qui ratione voluptatem sequi nesciunt</p>
</div>

<a class="btn" style="left:172px;top:1043px">Read more</a>
<a class="btn" style="left:521px;top:1043px">Read more</a>
<a class="btn" style="left:869px;top:1043px">Read more</a>
<a class="btn" style="left:172px;top:1367px">Read more</a>
<a class="btn" style="left:521px;top:1367px">Read more</a>
<a class="btn" style="left:869px;top:1367px">Read more</a>

<div class="vline" style="left:599px;top:1421px;height:87px"></div>
<div class="hline" style="left:166px;top:1506px;width:435px"></div>
<div class="vline" style="left:166px;top:1506px;height:35px"></div>

<!-- about -->
<div class="abs about-kicker">About us</div>
<h2 class="abs about-title">WELCOME TO <span>HARBOR CREST HOLDINGS</span></h2>
<p class="abs about-text">Nemo enim ipsam voluptatem quia voluptas sit aspernatur aut odit aut fugit, sed quia consequuntur magni dolores eos qui ratione voluptatem sequi nesciunt. Neque porro quisquam est, qui dolorem ipsum quia dolor sit amet, consectetur, adipisci velit, sed quia non numquam eius modi Nemo enim ipsam voluptatem</p>
<a class="btn" style="left:112px;top:1905px">Read more</a>
<div class="photo" style="left:768px;top:1622px;width:322px;height:357px;background:linear-gradient(160deg,#d8cfc6,#a89684 50%,#3c3a3e)" role="img" aria-label="Photo of a smiling businessman in a shirt and tie"></div>
<div class="photo" style="left:535px;top:1570px;width:324px;height:358px;background:linear-gradient(150deg,#eceae6,#c9c4ba 45%,#8a8a86 80%,#e1b64a)" role="img" aria-label="Photo of two colleagues reviewing documents at a laptop"></div>

<div class="vline" style="left:599px;top:1968px;height:113px"></div>

<!-- management -->
<div class="abs mgmt" role="img" aria-label="Teal tinted photo of an office meeting"></div>
<h2 class="abs mgmt-title">MANAGEMENT</h2>
<p class="abs mgmt-text">Nemo enim ipsam voluptatem quia voluptas sit aspernatur aut odit aut fugit, sed quia consequuntur magni dolores eos qui ratione voluptatem sequi nesciunt. Neque porro quisquam est, qui dolorem ipsum quia dolor sit amet, consectetur, adipisci velit, sed quia non numquam eius modi tempora incidunt ut labore et dolore magnam aliquam quaerat voluptatem. Nemo enim ipsam voluptatem quia voluptas sit aspernatur aut odit aut fugit, sed quia consequuntur magni dolores eos qui ratione voluptatem sequi nesciunt.</p>
<a class="btn btn-light" style="left:521px;top:2424px">Contact us</a>

<div class="vline" style="left:685px;top:2595px;height:139px"></div>

<!-- global outlook -->
<div class="photo" style="left:110px;top:2698px;width:427px;height:468px;background:linear-gradient(160deg,#e3e4e6,#9aa3ad 40%,#4b5a6e 75%,#2c3a52)" role="img" aria-label="Photo of a businessman holding a tablet over a city skyline with graph overlay"></div>
<h2 class="abs global-title">GLOBAL <span>OUTLOOK</span></h2>
<p class="abs global-text">Nemo enim ipsam voluptatem quia voluptas sit aspernatur aut odit aut fugit, sed quia consequuntur magni dolores eos qui ratione voluptatem sequi nesciunt. Neque porro quisquam est, qui dolorem ipsum quia dolor sit amet, consectetur, adipisci velit, sed quia non numquam eius modi Nemo enim ipsam voluptatem</p>
<a class="btn" style="left:600px;top:3033px">Read more</a>

<div class="vline" style="left:453px;top:3166px;height:157px"></div>

<!-- expertise -->
<h2 class="abs heading exp-title">EXPERTISE</h2>
<div class="card" style="left:111px;background:linear-gradient(170deg,#c9ccd0,#7c8796 55%,#33486e)" role="img" aria-label="Portrait photo of a team member in a denim shirt"></div>
<div class="card" style="left:356px;background:linear-gradient(170deg,#dfe3e6,#a9b1b9 55%,#1f232a)" role="img" aria-label="Portrait photo of a team member in a dark blazer"></div>
<div class="card card-hover" style="left:601px">
  <div class="card-name">DENNIS HALVER</div>
  <div class="card-role">Lorem ipsum dolor</div>
  <p class="card-text">Nemo enim ipsam voluptatem quia voluptas sit aspernatur aut odit aut fugit, sed quia consequuntur magni dolores eos qui ratione</p>
  <div class="socials"><i style="background:#3176b5"></i><i style="background:#f68e4d"></i></div>
</div>
<div class="card" style="left:846px;background:linear-gradient(170deg,#5a5350,#8d7b6e 45%,#e0892a)" role="img" aria-label="Portrait photo of a team member in an orange sweater"></div>

<!-- footer -->
<footer class="abs footer"></footer>
<div class="f-col" style="left:111px">
  <div class="f-head">QUICK LINKS</div>
  <ul class="f-links"><li>Home</li><li>About Us</li><li>Expertise</li><li>Global Outlook</li><li>Sectors</li><li>Management</li><li>Media</li><li>Contact Us</li></ul>
</div>
<div class="f-col" style="left:322px">
  <div class="f-head">COMPANY WORKS</div>
  <ul class="f-links"><li>Real Estate</li><li>E-Commerce</li><li>Healthcare</li><li>Beauty &amp; Personal Care</li><li>Technology</li><li>Resources</li></ul>
</div>
<div class="f-col" style="left:557px">
  <div class="f-head">ABOUT COMPANY</div>
  <ul class="f-links"><li>Team</li><li>Management</li><li>Media</li><li>Our Story</li></ul>
</div>
<div class="f-col" style="left:771px">
  <div class="f-head">SIGNUP TO OUR NEWSLETTER</div>
</div>
<div class="abs newsletter">Enter emaill address
  <svg width="22" height="22" viewBox="0 0 22 22"><circle cx="11" cy="11" r="11" fill="#00a990"/><path d="M5 11l12-5-4 12-2-5z" fill="#fff"/></svg>
</div>
<div class="abs contact" style="left:786px;top:3954px">
  <span class="dot"><svg width="16" height="12" viewBox="0 0 16 12"><rect width="16" height="12" rx="1" fill="#fff"/><path d="M1 1l7 6 7-6" stroke="#00a990" stroke-width="1.6" fill="none"/></svg></span>
  HarborCrestHoldings-example.com
</div>
<div class="abs contact" style="left:786px;top:4011px">
  <span class="dot"><svg width="16" height="16" viewBox="0 0 24 24"><path d="M6.6 10.8a15 15 0 006.6 6.6l2.2-2.2a1 1 0 011-.25 11.4 11.4 0 003.6.57 1 1 0 011 1V20a1 1 0 01-1 1A17 17 0 013 4a1 1 0 011-1h3.5a1 1 0 011 1c0 1.25.2 2.45.57 3.57a1 1 0 01-.25 1z" fill="#fff"/></svg></span>
  555-014-2290
</div>
<p class="abs copy">© <span>Harbor Crest Holdings</span>. 2020 All Rights Reserved</p>

</body>
</html>
```